Business Card Design

We service, sell & install vehicle hoists in automotive workshops & would like the colours royal blue or green incorporated into the design.

Industry/Entity Type

Automotive

Contact Information for Business Card

KLT Lifts
Equipment Sales & Service
Colin Dwyer 0412 558 913
Grant Oakes 0418 762 305
14 Tarn Crescent Wyndale Vic 3521
email: kltlifts@mailbox-example.com.au

```html
<!DOCTYPE html>
<html lang="en">
<head>
<meta charset="utf-8">
<title>KLT Lifts – Business Card</title>
<link rel="stylesheet" href="https://fonts.googleapis.com/css2?family=Open+Sans:wght@300;400;600;700&display=swap">
<style>
  :root {
    --backdrop: #262626;
    --card: #141414;
    --ink: #f2f2f2;
    --ink-soft: #d6d6d6;
    --royal-blue: #3a63e6;
  }
  * { margin: 0; padding: 0; box-sizing: border-box; }
  html, body {
    width: 1200px;
    height: 938px;
    overflow: hidden;
    background: var(--backdrop);
    font-family: "Open Sans", Arial, sans-serif;
  }
  .business-card {
    position: absolute;
    left: 255px;
    top: 253px;
    width: 692px;
    height: 430px;
    background: var(--card);
    color: var(--ink);
  }
  .brand {
    position: absolute;
    left: 41px;
    top: 44px;
    display: flex;
    align-items: center;
    gap: 14px;
  }
  .brand-name {
    font-weight: 700;
    font-size: 72px;
    line-height: 1;
    letter-spacing: -1px;
    color: var(--royal-blue);
  }
  .brand-tagline { display: flex; flex-direction: column; padding-top: 4px; }
  .brand-title {
    font-weight: 300;
    font-size: 40px;
    line-height: 40px;
    letter-spacing: 0.3px;
  }
  .brand-services {
    font-weight: 300;
    font-size: 23px;
    line-height: 28px;
    color: var(--ink-soft);
  }
  .holder-name {
    position: absolute;
    left: 42px;
    top: 242px;
    font-size: 28px;
    font-weight: 300;
    letter-spacing: 0.8px;
  }
  .holder-name strong { font-weight: 700; }
  .contact-list {
    position: absolute;
    right: 40px;
    top: 305px;
    list-style: none;
    text-align: right;
  }
  .contact-item {
    display: flex;
    justify-content: flex-end;
    align-items: center;
    gap: 12px;
    height: 28.5px;
    font-size: 18px;
    font-weight: 300;
    letter-spacing: 0.4px;
    color: var(--ink-soft);
  }
  .contact-icon { width: 14px; height: 16px; fill: none; stroke: var(--royal-blue); stroke-width: 1.6; }
</style>
</head>
<body>
  <main class="business-card">
    <div class="brand">
      <span class="brand-name">KLT</span>
      <div class="brand-tagline">
        <span class="brand-title">Lifts Equipment</span>
        <span class="brand-services">Sales &amp; Service</span>
      </div>
    </div>

    <p class="holder-name">GRANT <strong>OAKES</strong></p>

    <ul class="contact-list">
      <li class="contact-item">
        <span>0418 762 305</span>
        <svg class="contact-icon" viewBox="0 0 14 16" aria-hidden="true">
          <rect x="3" y="1" width="8" height="14" rx="1.5"/>
          <line x1="6" y1="12.5" x2="8" y2="12.5"/>
        </svg>
      </li>
      <li class="contact-item">
        <span>KLTLIFTS@MAILBOX-EXAMPLE.COM.AU</span>
        <svg class="contact-icon" viewBox="0 0 14 16" aria-hidden="true">
          <rect x="1.5" y="4.5" width="11" height="7.5" rx="0.8"/>
          <path d="M1.8 5l5.2 3.8L12.2 5"/>
        </svg>
      </li>
      <li class="contact-item">
        <span>TARN CRESCENT WYNDALE VIC 3521</span>
        <svg class="contact-icon" viewBox="0 0 14 16" aria-hidden="true">
          <path d="M7 15s-5-5.2-5-8.8A5 5 0 0 1 12 6.2C12 9.8 7 15 7 15z"/>
          <circle cx="7" cy="6.2" r="1.8"/>
        </svg>
      </li>
    </ul>
  </main>
</body>
</html>
```